Stylish business cards for KV7

To create an appealing and professional business card design for a WOMEN Owned Construction Supply Company.
2 sided card. Incorporate brand elements, curvy, colorful, sleek and bright. No solid white background. attached samples of styles added shapes/ribbons. Want something with that WOW that looks awesome, factor. It is a new logo, so feel free to mess with logo colors in the blue and teal factors that can look good with both dark and light background. If you want to try a watermark with just the KV7, without the "Supply" that might look cool to.

Industry/Entity Type

Women owned construction supply company

Contact Information for Business Card

Name, Title, and phone number and email, web page. maybe spot for qr code.

Font styles to use
Sans Serif

Requirements
Nice to have
• would love to see colors, maybe stylish ribbon dividers or some sort of 2 or 3 tone color card that compliments logo.
Should not have
• Please do not have all white background. Do not include Home/reale state/ or building images.

```html
<!DOCTYPE html>
<html lang="en">
<head>
<meta charset="utf-8">
<title>KV7 Supply – Business Card</title>
<link href="https://fonts.googleapis.com/css2?family=Montserrat:wght@400;500;700&display=swap" rel="stylesheet">
<style>
  :root {
    --stage: #1b1b1c;
    --navy: #1c3857;
    --teal: #2596be;
    --paper: #f4f4f4;
    --ink-light: #eef2f6;
  }
  * { margin: 0; padding: 0; box-sizing: border-box; }
  html, body {
    width: 1200px; height: 1059px; overflow: hidden;
    background: var(--stage);
    font-family: "Montserrat", sans-serif;
  }
  .canvas { position: relative; width: 1200px; height: 1059px; }

  .card {
    position: absolute;
    width: 690px; height: 392px;
    border-radius: 18px;
    overflow: hidden;
  }
  .card--front { left: 256px; top: 89px; background: var(--paper); }
  .card--back  { left: 255px; top: 548px; background: var(--navy); }

  .card__shape { position: absolute; inset: 0; width: 100%; height: 100%; }

  .brand-name {
    position: absolute;
    font-weight: 700;
    white-space: nowrap;
    letter-spacing: 0.5px;
  }
  .card--front .brand-name {
    left: 40px; top: 178px;
    font-size: 34px; color: var(--navy);
  }
  .card--back .brand-name {
    left: 0; right: 0; top: 162px; text-align: center;
    font-size: 52px; color: var(--ink-light);
  }

  .contact {
    position: absolute; left: 380px; top: 96px;
    width: 236px; color: var(--ink-light);
  }
  .contact__name {
    font-size: 20px; font-weight: 700; color: var(--teal);
    letter-spacing: 0.3px; line-height: 24px;
  }
  .contact__title { font-size: 13.5px; font-weight: 400; line-height: 18px; }
  .contact__rule { height: 1px; background: var(--teal); margin: 12px 0 14px; }
  .contact__address { font-size: 13.5px; line-height: 20px; }
  .contact__list { list-style: none; }
  .contact__item {
    display: flex; align-items: center; gap: 7px;
    font-size: 13.5px; line-height: 24.5px;
  }
  .contact__icon { width: 12px; height: 12px; flex: none; }
</style>
</head>
<body>
<main class="canvas">

  <section class="card card--front" aria-label="Business card front">
    <svg class="card__shape" viewBox="0 0 690 392" preserveAspectRatio="none" aria-hidden="true">
      <path d="M336 52 C 272 150, 272 290, 350 392 L 368 392 C 300 290, 296 160, 336 52 Z" fill="var(--teal)"/>
      <path d="M385 0 C 290 120, 290 270, 378 392 L 690 392 L 690 0 Z" fill="var(--navy)"/>
    </svg>

    <div class="brand-name">KV7 Supply</div>

    <div class="contact">
      <div class="contact__name">DANA KELLER</div>
      <div class="contact__title">CEO/Founder</div>
      <div class="contact__rule"></div>
      <div class="contact__address">P.O Box 4127 Harbour Road<br>Westvale AB 20481</div>
      <div class="contact__rule"></div>
      <ul class="contact__list">
        <li class="contact__item">
          <svg class="contact__icon" viewBox="0 0 12 12" aria-hidden="true"><path d="M2.4 0.8 L4.2 0.5 L5 3.2 L3.8 4.2 C4.4 5.8 5.9 7.4 7.6 8.1 L8.6 6.9 L11.3 7.8 L11 9.6 C10.8 10.8 9.6 11.4 8.4 11 C4.8 9.9 2 7.1 0.9 3.4 C0.6 2.2 1.2 1 2.4 0.8 Z" fill="var(--teal)"/></svg>
          555.010.2468
        </li>
        <li class="contact__item">
          <svg class="contact__icon" viewBox="0 0 12 12" aria-hidden="true"><rect x="0.5" y="2" width="11" height="8" fill="var(--teal)"/><path d="M0.8 2.4 L6 6.6 L11.2 2.4" stroke="var(--navy)" stroke-width="1" fill="none"/></svg>
          info@kv7supply.com.au
        </li>
        <li class="contact__item">
          <svg class="contact__icon" viewBox="0 0 12 12" aria-hidden="true"><g fill="none" stroke="var(--teal)" stroke-width="1"><circle cx="6" cy="6" r="5.2"/><ellipse cx="6" cy="6" rx="2.3" ry="5.2"/><path d="M0.8 6 H11.2 M1.6 3.4 H10.4 M1.6 8.6 H10.4"/></g></svg>
          www.kv7supply.com.au
        </li>
      </ul>
    </div>
  </section>

  <section class="card card--back" aria-label="Business card back">
    <div class="brand-name">KV7 Supply</div>
  </section>

</main>
</body>
</html>
```